Rafiq Donhelm Business Card

I would like an elegant business card design in both english and arabic.

Ideally a logo design with my name in Arabic (could be a tiger for example)

It should have my Name : Rafiq Donhelm
Title: Advisor / Investor
Tel. UAE +971 528 470 213
UK +44 7852 906 418
Email. rafdonhelm412@mailvento.com

I am an active angle investor and have many business interests in the TMT space and invest globally, the design needs to be fresh, elegant and striking.

The design should be catching and grab one's attention when they view the card.

Front card should be in English and Reverse in Arabic....

Target Market(s)

Global Investors, CEO's

Industry/Entity Type

Business

Contact Information for Business Card

Title: Advisor / Investor
Tel. UAE +971 528 470 213
UK +44 7852 906 418

Font styles to use
Serif
Other font styles liked:
• Palantino

Requirements
Must have
• A striking design with a play of my name in Arabic, could be my name that is designed as a tiger for example

```html
<!DOCTYPE html>
<html lang="en">
<head>
<meta charset="utf-8">
<title>Rafiq Donhelm Business Card</title>
<link rel="stylesheet" href="https://fonts.googleapis.com/css2?family=Libre+Baskerville:wght@400;700&family=Noto+Naskh+Arabic:wght@500;700&family=Open+Sans:wght@400;600&display=swap">
<style>
  :root {
    --stage: #000000;
    --card: #ffffff;
    --ink: #1a1a1a;
    --mark: #2b2b2b;
  }
  * { margin: 0; padding: 0; box-sizing: border-box; }
  html, body {
    width: 1200px;
    height: 451px;
    overflow: hidden;
    background: var(--stage);
  }
  .stage {
    position: relative;
    width: 1200px;
    height: 451px;
  }
  .card {
    position: absolute;
    top: 42px;
    width: 542px;
    height: 353px;
    background: var(--card);
    color: var(--ink);
  }
  .card--front { left: 39px; }
  .card--back { left: 609px; }

  .brand-dot {
    position: absolute;
    border-radius: 50%;
    background: var(--mark);
  }
  .card--front .brand-dot { left: 440px; top: 112px; width: 82px; height: 82px; }
  .card--back .brand-dot { left: 412px; top: 110px; width: 92px; height: 92px; }

  .name-en {
    position: absolute;
    right: 112px;
    top: 150px;
    font-family: "Libre Baskerville", "Palatino Linotype", serif;
    font-weight: 400;
    font-size: 40px;
    line-height: 1;
    letter-spacing: 0.5px;
    white-space: nowrap;
    text-transform: uppercase;
  }
  .title-en {
    position: absolute;
    right: 123px;
    top: 204px;
    font-family: "Libre Baskerville", "Palatino Linotype", serif;
    font-size: 17px;
    line-height: 1;
    white-space: nowrap;
  }
  .contact {
    position: absolute;
    right: 16px;
    font-family: "Open Sans", Arial, sans-serif;
    font-weight: 600;
    font-size: 17px;
    line-height: 1;
    white-space: nowrap;
    text-align: right;
  }
  .contact--uae { top: 290px; }
  .contact--uk { top: 313px; }
  .contact--email { top: 312px; right: 14px; font-weight: 400; }

  .name-ar {
    position: absolute;
    right: 144px;
    top: 72px;
    font-family: "Noto Naskh Arabic", "Times New Roman", serif;
    font-weight: 700;
    font-size: 82px;
    line-height: 1.2;
    white-space: nowrap;
  }
  .title-ar {
    position: absolute;
    right: 141px;
    top: 176px;
    font-family: "Noto Naskh Arabic", "Times New Roman", serif;
    font-weight: 500;
    font-size: 52px;
    line-height: 1.2;
    white-space: nowrap;
  }
</style>
</head>
<body>
<main class="stage">
  <section class="card card--front" lang="en">
    <h1 class="name-en">Rafiq Donhelm</h1>
    <div class="brand-dot" aria-hidden="true"></div>
    <p class="title-en">Advisor / Investor</p>
    <p class="contact contact--uae">UAE +971 528 470 213</p>
    <p class="contact contact--uk">UK +44 7852 906 418</p>
  </section>

  <section class="card card--back" lang="ar" dir="rtl">
    <h2 class="name-ar">رفيق دونهلم</h2>
    <div class="brand-dot" aria-hidden="true"></div>
    <p class="title-ar">مستثمر/المستشار</p>
    <p class="contact contact--email" dir="ltr">rafdonhelm412@mailvento.com</p>
  </section>
</main>
</body>
</html>
```